New Fun, Positive, energised looking Business Card Needed for High Achiever Coach

I am looking for a two sided full colour business card. I am self employed and have recently re branded my 1-2-1 work re-vitalising high achievers. My target client base for these cards is therefore high achievers - usually aged 40 -55, they are often entrepreneurs, CEO or work in banking and finance and 2/3 are male. I work with them on 90 day or 6 month coaching programs to help them live their success in a healthier, more sustainable and fulfiiled way. They pay for this privately so though they are corporate types the cards need not look 'corporate'. I want to portray the idea of transformation, vitality and re-connecting.
You can get a feel for the look I like on my new website: morvenlisk.co.uk
I want to use this logo with strapline (Re-Vitalising High Achievers) (I purchased off Logoharbor) and font/ colours (the turquoise and green).
Details to include on the card:
www.morvenlisk.co.uk
+44 7915 302618
morven@morvenlisk.co.uk
skype: morvenlisk
I'd also like to include:
Do you struggle to switch off? Want to be healthier and feel fitter? Want closer relationships? More clarity over the direction you are headed? I can help you do these things using integrated mind-body techniques. Visit morvenlisk.co.uk TODAY to apply for a FREE Breakthrough session.
BUT if that is too much text for a card I am open to advice/ammendments.
Updates
Thanks for your design - I am considering them. PLease change the wording to :

```html
<!DOCTYPE html>
<html lang="en">
<head>
<meta charset="utf-8">
<title>Morven Lisk – Business Card</title>
<link rel="stylesheet" href="https://fonts.googleapis.com/css2?family=Source+Sans+3:wght@400;600;700&display=swap">
<style>
  :root {
    --turquoise: #00a3c6;
    --green: #62b867;
    --ink: #2b2b2b;
    --paper: #ffffff;
    --backdrop: #e8e8e6;
    --faint: #efefef;
  }
  html, body {
    margin: 0;
    width: 1109px;
    height: 1200px;
    overflow: hidden;
    background: var(--backdrop);
    font-family: "Source Sans 3", "Myriad Pro", sans-serif;
  }
  .canvas { position: relative; width: 1109px; height: 1200px; }
  .card {
    position: absolute;
    left: 135px;
    width: 838px;
    height: 478px;
    background: var(--paper);
    overflow: hidden;
    box-shadow: 0 3px 10px rgba(0,0,0,0.18);
  }
  .card--front { top: 96px; }
  .card--back { top: 612px; }

  .wave { position: absolute; inset: 0; width: 838px; height: 478px; }

  .brand { position: absolute; left: 48px; top: 196px; }
  .brand__name {
    display: flex; align-items: center; gap: 12px;
    font-weight: 700; font-size: 38px; color: var(--turquoise);
    line-height: 1;
  }
  .brand__dot { width: 26px; height: 26px; border-radius: 50%; background: var(--green); }
  .brand__strapline {
    margin-top: 8px; font-size: 18px; color: var(--turquoise); font-weight: 400;
  }

  .contact {
    position: absolute; right: 42px; top: 296px;
    color: var(--paper); font-size: 21px; text-align: right;
  }
  .contact__line { display: flex; justify-content: flex-end; align-items: center; gap: 8px; height: 38px; }
  .contact__icon { width: 16px; height: 16px; }
  .contact__social { margin-top: 14px; gap: 6px; }
  .contact__social span { margin-right: 6px; }
  .social-square { width: 22px; height: 22px; border-radius: 3px; background: #5a8fd0; border: 1px solid rgba(255,255,255,0.7); }

  .back__mark {
    position: absolute; left: 0; right: 0; top: 160px;
    text-align: center; font-weight: 700; font-size: 120px; color: var(--faint);
    line-height: 1; white-space: nowrap;
  }
  .back__copy {
    position: relative; text-align: center; color: var(--ink);
    font-size: 24px; line-height: 38px; padding-top: 76px;
  }
  .back__copy p { margin: 0; }
  .back__copy p + p { margin-top: 14px; }
  .back__copy .gap { margin-top: 16px; }
  .back__copy strong { font-weight: 700; }
</style>
</head>
<body>
<main class="canvas">

  <section class="card card--front" aria-label="Business card front">
    <svg class="wave" viewBox="0 0 838 478" aria-hidden="true">
      <path d="M0,376 C140,372 280,360 410,322 C300,356 150,372 0,386 Z" fill="var(--turquoise)"/>
      <path d="M0,420 C210,428 380,414 520,330 C640,258 740,232 838,228 L838,478 L0,478 Z" fill="var(--turquoise)"/>
      <path d="M0,402 C205,410 372,398 508,316 C628,244 736,214 838,208" fill="none" stroke="var(--green)" stroke-width="11"/>
      <path d="M560,320 C650,268 740,246 838,244" fill="none" stroke="var(--paper)" stroke-width="6" opacity="0.9"/>
      <path d="M600,210 C680,192 760,186 838,188 L838,198 C760,196 690,200 600,210 Z" fill="var(--turquoise)"/>
    </svg>

    <div class="brand">
      <div class="brand__name"><span class="brand__dot"></span>Morven Lisk</div>
      <div class="brand__strapline">Re-Vitalising High Achievers</div>
    </div>

    <div class="contact">
      <div class="contact__line">
        <svg class="contact__icon" viewBox="0 0 16 16" aria-hidden="true"><circle cx="8" cy="8" r="7" fill="none" stroke="#fff" stroke-width="1.4"/><path d="M5.5 4.5 l1.5 0 0.7 2 -1 0.8 c0.5 1 1.2 1.7 2.2 2.2 l0.8 -1 2 0.7 0 1.5 c-4 0.4 -6.6 -2.2 -6.2 -6.2z" fill="#fff"/></svg>
        +44 7915 302618
      </div>
      <div class="contact__line">
        <svg class="contact__icon" viewBox="0 0 16 16" aria-hidden="true"><rect x="1" y="4" width="14" height="9" rx="1" fill="#fff"/><path d="M1.5 4.5 L8 9 L14.5 4.5" fill="none" stroke="var(--turquoise)" stroke-width="1.3"/></svg>
        morven@morvenlisk.co.uk
      </div>
      <div class="contact__line">
        <svg class="contact__icon" viewBox="0 0 16 16" aria-hidden="true"><g fill="none" stroke="#fff" stroke-width="1.3"><circle cx="8" cy="8" r="6.5"/><ellipse cx="8" cy="8" rx="3" ry="6.5"/><path d="M1.5 8h13M2.5 5h11M2.5 11h11"/></g></svg>
        www.morvenlisk.co.uk
      </div>
      <div class="contact__line contact__social">
        <span>Follow us on</span>
        <i class="social-square"></i><i class="social-square"></i><i class="social-square"></i><i class="social-square"></i>
      </div>
    </div>
  </section>

  <section class="card card--back" aria-label="Business card back">
    <div class="back__mark" aria-hidden="true">Morven Lisk</div>
    <div class="back__copy">
      <p>Do you struggle to switch off?<br>
      Want to be healthier and&nbsp; feel fitter?<br>
      Want closer relationships?<br>
      More clarity over the direction you are headed?</p>
      <p class="gap">Let me help you reach these goals using integrated<br>mind-body techniques.</p>
      <p>Visit <strong>morvenlisk.co.uk</strong>&nbsp; TODAY to apply for a<br>FREE Breakthrough session.</p>
    </div>
  </section>

</main>
</body>
</html>
```